Furniture & Lighting Wholesaler Needs a Product Catalogue/Look Book

Our company, Vostre Merchant Co, imports quality hand-made furniture, lighting and decor from South Africa. Our products are well-designed and are designed to be used in up-market hotels and homes. Our primary customers are small- to medium-size retail shops.
We require a +/- 14-16 page look book (concept as per attached image) that will be used both in hard-copy and online. We have all of the necessary high-res images, descriptions/text etc. We need you to propose several design concepts from which we can choose, and then execute the design.
Please visit our website www.vostremerchant.example to see the products and their descriptions, as well as to get a feel for our style. Thank you for looking at our project!
Target Market(s)
Boutique Furniture Stores; Interior Designers
Industry/Entity Type
It Company
Font styles to use
Other font styles liked:
- Bauer Bodini and Open Sans Condensed
Look and feel
Each slider illustrates characteristics of the customer's brand and the style your logo design should communicate.

```html
<!DOCTYPE html>
<html lang="en">
<head>
<meta charset="utf-8">
<title>Vostre Merchant Co — Look Book Spread</title>
<link href="https://fonts.googleapis.com/css2?family=Open+Sans:wght@300;400;600;700&display=swap" rel="stylesheet">
<style>
  :root{
    --backdrop:#d3d3d3;
    --paper:#fbfbfb;
    --gold:#b3a477;
    --gold-dark:#9c8d5f;
    --ink:#2b2b2b;
    --muted:#8a8a8a;
    --band:#dedede;
    --card-shadow:#e4e4e4;
    --corner:#4a4a4a;
  }
  *{box-sizing:border-box;margin:0;padding:0}
  html,body{width:1200px;height:800px;overflow:hidden}
  body{background:var(--backdrop);font-family:"Open Sans",Arial,sans-serif;color:var(--ink);position:relative}
  .spread{position:absolute;left:30px;top:185px;width:1140px;height:430px;display:flex;box-shadow:0 6px 18px rgba(0,0,0,.12)}
  .page{position:relative;width:570px;height:430px;background:var(--paper);overflow:hidden}
  .page--left{background:linear-gradient(90deg,var(--paper) 90%,#ececec 100%)}
  .page--right{background:linear-gradient(90deg,#ececec 0%,var(--paper) 10%)}
  .band{position:absolute;height:74px;background:linear-gradient(90deg,#e9e9e9,var(--band) 40%,#e2e2e2)}
  .page--left .band{left:110px;right:0;top:172px;border-radius:37px 0 0 37px}
  .page--right .band{left:0;width:480px;top:165px;border-radius:0 37px 37px 0}
  .card{position:absolute}
  .card::before{content:"";position:absolute;inset:-6px -8px 6px 8px;background:var(--card-shadow);border-radius:16px;transform:rotate(-6deg)}
  .card__frame{position:relative;width:100%;height:100%;background:#fff;border:2px solid var(--gold);border-radius:14px;padding:12px}
  .card__photo{width:100%;height:100%;border-radius:6px}
  .photo--stool{background:radial-gradient(circle at 50% 45%,#6b6457 0%,#3a3630 35%,#fff 70%)}
  .photo--chair{background:radial-gradient(circle at 50% 50%,#5f6660 0%,#3c423d 40%,#fff 72%)}
  .photo--trunk-dark{background:radial-gradient(circle at 50% 50%,#3c3a36 0%,#24221f 50%,#fff 78%)}
  .photo--trunk-tan{background:linear-gradient(160deg,#b8a88a,#8e7c62 60%,#a49379)}
  .info{position:absolute;width:108px}
  .info__name{font-size:8.5px;font-weight:600;color:var(--gold);letter-spacing:.3px;text-transform:uppercase}
  .info__desc{font-size:7px;font-weight:700;line-height:1.25;margin-top:2px}
  .price{display:inline-block;background:var(--gold);color:#fff;font-weight:300;font-size:12px;padding:2px 10px;margin:6px 0 5px;box-shadow:2px 2px 0 rgba(0,0,0,.15)}
  .bullets{list-style:none;font-size:5px;color:var(--muted);line-height:1.5}
  .bullets li::before{content:"• "}
  .deluxe{position:absolute;width:170px}
  .deluxe__title{font-size:11px;color:var(--gold);letter-spacing:.5px;font-weight:400}
  .deluxe__text{font-size:7px;font-weight:600;line-height:1.3;margin-top:3px}
  .band-list{position:absolute;list-style:none;font-size:7px;color:#777;line-height:1.5}
  .band-list li::before{content:"• "}
  .tab{position:absolute;width:24px;background:var(--gold)}
  .page--left .tab{left:0;top:255px;height:150px;border-radius:0 24px 24px 0}
  .page--right .tab{right:0;top:20px;height:160px;border-radius:24px 0 0 24px}
  .folio{position:absolute;width:26px;height:26px;background:var(--corner);color:#ddd;font-size:8px;display:flex;align-items:center;justify-content:center}
  .page--left .folio{left:0;bottom:0;border-radius:0 14px 0 0}
  .page--right .folio{right:0;top:180px;border-radius:14px 0 0 14px}
  .site{position:absolute;bottom:10px;display:flex;align-items:center;gap:6px;font-size:6.5px;color:var(--muted)}
  .site__mark{width:9px;height:9px;border:1.5px solid var(--ink)}
  .page--left .site{right:30px}
  .page--right .site{left:30px}
</style>
</head>
<body>
<main class="spread">
  <!-- Page 6 -->
  <section class="page page--left">
    <div class="band"></div>

    <div class="card" style="left:60px;top:40px;width:120px;height:120px"><div class="card__frame"><div class="card__photo photo--stool" role="img" aria-label="Tripod side table with studded round top"></div></div></div>
    <div class="info" style="left:195px;top:42px">
      <p class="info__name">Product Name</p>
      <p class="info__desc">Faccupta ipiim excearum rae expligent lam qui occulpa rchicie ndesequ latur</p>
      <span class="price">$59.99</span>
      <ul class="bullets"><li>Sint labor simolluptat ulles</li><li>Es maximus si num</li><li>Acerepedi moluptaquae</li><li>Pitaqui dipiciet que</li></ul>
    </div>

    <div class="card" style="left:330px;top:18px;width:110px;height:110px"><div class="card__frame"><div class="card__photo photo--chair" role="img" aria-label="Upholstered armchair with round back"></div></div></div>
    <div class="info" style="left:455px;top:14px">
      <p class="info__name">Product Name</p>
      <p class="info__desc">Faccupta ipiim excearum rae expligent lam qui occulpa rchicie ndesequ latur</p>
      <span class="price">$59.99</span>
      <ul class="bullets"><li>Sint labor simolluptat ulles</li><li>Es maximus si num</li><li>Acerepedi moluptaquae</li><li>Pitaqui dipiciet que</li></ul>
    </div>

    <div class="deluxe" style="left:165px;top:188px">
      <p class="deluxe__title">DELUXE</p>
      <p class="deluxe__text">Faccupta ipiim excearum rae expligent lam qui occulpa rchicie ndesequ latur fature dit derioriti ta dolesec aborruptur</p>
    </div>
    <span class="price" style="position:absolute;left:350px;top:200px">$59.99</span>
    <ul class="band-list" style="left:430px;top:186px"><li>Sint labor simolluptat ulles expellacit</li><li>Es maximus si num ad etus</li><li>Acerepedi moluptaquae</li><li>Pitaqui dipiciet que dit dolor</li></ul>

    <div class="card" style="left:42px;top:236px;width:68px;height:68px"><div class="card__frame" style="padding:7px"><div class="card__photo photo--trunk-dark" role="img" aria-label="Dark studded leather trunk"></div></div></div>

    <div class="card" style="left:72px;top:282px;width:130px;height:130px"><div class="card__frame"><div class="card__photo photo--chair" role="img" aria-label="Upholstered armchair with round back"></div></div></div>
    <div class="info" style="left:218px;top:282px">
      <p class="info__name">Product Name</p>
      <p class="info__desc">Faccupta ipiim excearum rae expligent lam qui occulpa rchicie ndesequ latur</p>
      <span class="price">$59.99</span>
      <ul class="bullets"><li>Sint labor simolluptat ulles</li><li>Es maximus si num</li><li>Acerepedi moluptaquae</li><li>Pitaqui dipiciet que</li></ul>
    </div>

    <div class="card" style="left:340px;top:262px;width:120px;height:120px"><div class="card__frame"><div class="card__photo photo--stool" role="img" aria-label="Tripod side table with studded round top"></div></div></div>
    <div class="info" style="left:472px;top:258px;width:92px">
      <p class="info__name">Product Name</p>
      <p class="info__desc">Faccupta ipiim excearum rae expligent lam qui occulpa rchicie</p>
      <span class="price">$59.99</span>
      <ul class="bullets"><li>Sint labor simolluptat ulles</li><li>Es maximus si num</li><li>Acerepedi moluptaquae</li><li>Pitaqui dipiciet que</li></ul>
    </div>

    <div class="tab"></div>
    <div class="folio">6</div>
    <p class="site"><span class="site__mark"></span>www.vostremerchant.example</p>
  </section>

  <!-- Page 7 -->
  <section class="page page--right">
    <div class="band"></div>

    <div class="card" style="left:35px;top:55px;width:110px;height:110px"><div class="card__frame"><div class="card__photo photo--stool" role="img" aria-label="Tripod side table with studded round top"></div></div></div>
    <div class="info" style="left:158px;top:50px">
      <p class="info__name">Product Name</p>
      <p class="info__desc">Faccupta ipiim excearum rae expligent lam qui occulpa rchicie ndesequ latur</p>
      <span class="price">$59.99</span>
      <ul class="bullets"><li>Sint labor simolluptat ulles</li><li>Es maximus si num</li><li>Acerepedi moluptaquae</li><li>Pitaqui dipiciet que</li></ul>
    </div>

    <div class="card" style="left:275px;top:22px;width:105px;height:105px"><div class="card__frame"><div class="card__photo photo--stool" role="img" aria-label="Tripod side table with studded round top"></div></div></div>
    <div class="info" style="left:392px;top:14px">
      <p class="info__name">Product Name</p>
      <p class="info__desc">Faccupta ipiim excearum rae expligent lam qui occulpa rchicie ndesequ latur</p>
      <span class="price">$59.99</span>
      <ul class="bullets"><li>Sint labor simolluptat ulles</li><li>Es maximus si num</li><li>Acerepedi moluptaquae</li><li>Pitaqui dipiciet que</li></ul>
    </div>

    <div class="card" style="left:478px;top:118px;width:66px;height:66px"><div class="card__frame" style="padding:7px"><div class="card__photo photo--trunk-dark" role="img" aria-label="Dark studded leather trunk"></div></div></div>

    <div class="deluxe" style="left:30px;top:188px">
      <p class="deluxe__title">DELUXE</p>
      <p class="deluxe__text">Faccupta ipiim excearum rae expligent lam qui occulpa rchicie ndesequ latur fature dit dolesec aborruptur</p>
    </div>
    <span class="price" style="position:absolute;left:215px;top:192px">$59.99</span>
    <ul class="band-list" style="left:300px;top:176px"><li>Sint labor simolluptat ulles</li><li>Es maximus si num ad etus</li><li>Acerepedi moluptaquae</li><li>Pitaqui dipiciet que dit dolor</li></ul>

    <div class="card" style="left:85px;top:262px;width:130px;height:130px"><div class="card__frame"><div class="card__photo photo--trunk-tan" role="img" aria-label="Tan leather trunk with straps"></div></div></div>
    <div class="info" style="left:230px;top:256px">
      <p class="info__name">Product Name</p>
      <p class="info__desc">Faccupta ipiim excearum rae expligent lam qui occulpa rchicie ndesequ latur</p>
      <span class="price">$59.99</span>
      <ul class="bullets"><li>Sint labor simolluptat ulles</li><li>Es maximus si num</li><li>Acerepedi moluptaquae</li><li>Pitaqui dipiciet que</li></ul>
    </div>

    <div class="card" style="left:345px;top:255px;width:115px;height:115px"><div class="card__frame"><div class="card__photo photo--trunk-tan" role="img" aria-label="Tan leather trunk with straps"></div></div></div>
    <div class="info" style="left:472px;top:250px;width:85px">
      <p class="info__name">Product Name</p>
      <p class="info__desc">Faccupta ipiim excearum rae expligent lam qui occulpa</p>
      <span class="price">$59.99</span>
      <ul class="bullets"><li>Sint labor simolluptat ulles</li><li>Es maximus si num</li><li>Acerepedi moluptaquae</li><li>Pitaqui dipiciet que</li></ul>
    </div>

    <div class="tab"></div>
    <div class="folio">7</div>
    <p class="site"><span class="site__mark"></span>www.vostremerchant.example</p>
  </section>
</main>
</body>
</html>
```